Business cards for Zestcycle

We need a business card layout for our new bike and e-bike rental (we also sell used e-bikes and bike accessories). The logo already exists.

```html
<!DOCTYPE html>
<html lang="de">
<head>
<meta charset="utf-8">
<title>Zestcycle – Visitenkarte</title>
<link rel="stylesheet" href="https://fonts.googleapis.com/css2?family=Open+Sans:wght@300;400;600&display=swap">
<style>
  :root {
    --canvas: #e9ebea;
    --card: #f6f6f5;
    --ink: #1c3139;
    --panel: #1c3139;
    --accent: #4fbf9f;
    --on-panel: #f2f5f4;
  }
  * { box-sizing: border-box; margin: 0; padding: 0; }
  html, body {
    width: 1200px; height: 900px; overflow: hidden;
    background: var(--canvas);
    font-family: "Open Sans", Arial, sans-serif;
  }
  .card {
    position: absolute; left: 150px; top: 170px;
    width: 900px; height: 560px;
    background: var(--card);
    box-shadow: 0 12px 36px rgba(0,0,0,.14);
    overflow: hidden;
  }
  .brand {
    position: absolute; left: 0; top: 0; width: 440px; height: 560px;
    display: flex; flex-direction: column; align-items: center;
  }
  .brand-dot {
    margin-top: 170px;
    width: 46px; height: 46px; border-radius: 50%;
    background: var(--accent);
  }
  .brand-name {
    margin-top: 26px;
    font-size: 72px; font-weight: 400; letter-spacing: 1px;
    color: var(--accent); line-height: 1;
  }
  .brand-tagline {
    margin-top: 40px;
    font-size: 23px; font-weight: 600; color: var(--ink);
  }
  .panel-shape { position: absolute; inset: 0; }
  .contact {
    position: absolute; right: 44px; top: 140px;
    text-align: right; color: var(--on-panel);
  }
  .contact-name {
    font-size: 31px; font-weight: 400; color: var(--accent);
    letter-spacing: .5px; line-height: 1.1;
  }
  .contact-role { font-size: 24px; font-weight: 400; line-height: 1.35; }
  .contact-list { list-style: none; margin-top: 64px; }
  .contact-list li {
    font-size: 24px; line-height: 33px;
    display: flex; justify-content: flex-end; align-items: center; gap: 4px;
  }
  .contact-list svg { width: 20px; height: 20px; fill: var(--accent); }
  .contact-address { margin-top: 12px; font-size: 24px; line-height: 34px; }
</style>
</head>
<body>
  <main class="card">
    <section class="brand">
      <div class="brand-dot"></div>
      <div class="brand-name">ZESTCYCLE</div>
      <div class="brand-tagline">frisch losrollen</div>
    </section>

    <svg class="panel-shape" viewBox="0 0 900 560" width="900" height="560" aria-hidden="true">
      <path fill="var(--accent)" transform="translate(-10 6)"
        d="M665,0 C610,20 585,70 595,125 C520,140 470,200 470,260 C470,320 500,355 530,370 C470,395 450,450 480,500 C500,535 540,555 600,560 L900,560 L900,0 Z"/>
      <path fill="var(--panel)"
        d="M665,0 C610,20 585,70 595,125 C520,140 470,200 470,260 C470,320 500,355 530,370 C470,395 450,450 480,500 C500,535 540,555 600,560 L900,560 L900,0 Z"/>
    </svg>

    <section class="contact">
      <div class="contact-name">LUKAS BRENNER</div>
      <div class="contact-role">Managing Director</div>
      <ul class="contact-list">
        <li>030-555 208 417
          <svg viewBox="0 0 20 20"><path d="M3 7c0-3 3-4 7-4s7 1 7 4v1h-4V6.5H7V8H3zM5 9h10l2 7H3z"/></svg>
        </li>
        <li>0170-555 36 92
          <svg viewBox="0 0 20 20"><path d="M6 1h8a1 1 0 0 1 1 1v16a1 1 0 0 1-1 1H6a1 1 0 0 1-1-1V2a1 1 0 0 1 1-1zm1 2v12h6V3zm3 13a1 1 0 1 0 0 2 1 1 0 0 0 0-2z"/></svg>
        </li>
        <li>info@zestcycle.example
          <svg viewBox="0 0 20 20"><path d="M2 4h16v12H2zm1.5 1.5L10 11l6.5-5.5z"/></svg>
        </li>
        <li>www.zestcycle.example
          <svg viewBox="0 0 20 20"><circle cx="10" cy="10" r="8"/></svg>
        </li>
      </ul>
      <div class="contact-address">12345, Address Goes Here<br>Country Name, 123456</div>
    </section>
  </main>
</body>
</html>
```